New business card/stationary for a consulting company

I am looking for a clean and very professional looking business card for my consulting company as well as corresponding stationary. I am uploading our logo. I like simple and powerful for the feel. No graphics but I am open on everything else. Below is my contact information but would like the final to be in a version I can add my employees information into and print. Thank you.

Daniel Whitcombe
dan@ferncliffadvisory.com
2870 North 9th Avenue, Summit Floor, Elm Ridge, Illinois 60531
www.ferncliffadvisory.com

Industry/Entity Type

Consulting

Contact Information for Business Card

Daniel Whitcombe
dan@ferncliffadvisory.com
www.ferncliffadvisory.com

Font styles to use
Serif
Sans Serif

Requirements
Must have
• Our logo and the business card details.
Nice to have
• our website www.ferncliffadvisory.com

```html
<!DOCTYPE html>
<html lang="en">
<head>
<meta charset="utf-8">
<title>Ferncliff Advisory — Business Card</title>
<link href="https://fonts.googleapis.com/css2?family=Montserrat:wght@300;400;500;700&display=swap" rel="stylesheet">
<style>
  :root {
    --brand-blue: #0b0ba6;
    --paper: #ffffff;
    --ink: #2a2a2a;
    --backdrop: #eeeeee;
  }
  * { box-sizing: border-box; margin: 0; padding: 0; }
  html, body { width: 1200px; height: 900px; overflow: hidden; }
  body {
    background: var(--backdrop);
    font-family: "Montserrat", sans-serif;
    display: flex;
    align-items: center;
    justify-content: center;
    gap: 40px;
  }
  .card {
    width: 560px;
    height: 320px;
    position: relative;
    box-shadow: 0 4px 14px rgba(0,0,0,0.12);
    overflow: hidden;
  }

  /* Front: blue */
  .card--front {
    background: var(--brand-blue);
    color: var(--paper);
    display: flex;
    flex-direction: column;
    align-items: center;
    justify-content: center;
  }
  .brand {
    display: flex;
    align-items: center;
    gap: 14px;
  }
  .brand__square { width: 26px; height: 26px; background: currentColor; }
  .brand__name {
    font-weight: 400;
    letter-spacing: 0.06em;
    text-transform: uppercase;
    line-height: 1;
  }
  .card--front .brand__name { font-size: 30px; }
  .front__rule {
    display: flex;
    align-items: center;
    gap: 12px;
    width: 440px;
    margin-top: 22px;
  }
  .front__rule::before, .front__rule::after {
    content: ""; flex: 1; height: 2px; background: var(--paper);
  }
  .front__site { font-size: 11px; font-weight: 700; letter-spacing: 0.02em; }
  .front__base-line {
    position: absolute; left: 72px; bottom: 34px; width: 230px; height: 2px; background: var(--paper);
  }

  /* Back: white */
  .card--back { background: var(--paper); color: var(--ink); }
  .card--back .brand {
    position: absolute; top: 48px; left: 0; right: 0; justify-content: center;
    color: var(--brand-blue);
  }
  .card--back .brand__name { font-size: 24px; }
  .card--back .brand__square { width: 20px; height: 20px; }
  .back__body {
    position: absolute; top: 118px; left: 30px; right: 30px;
    display: flex; align-items: center;
  }
  .person { width: 250px; text-align: right; padding-right: 22px; }
  .person__name { color: var(--brand-blue); font-weight: 700; font-size: 20px; }
  .person__role { color: var(--brand-blue); font-weight: 500; font-size: 12px; margin-top: 4px; }
  .person__address { font-size: 11px; line-height: 1.6; margin-top: 10px; }
  .back__divider { width: 1.5px; height: 110px; background: var(--brand-blue); }
  .contacts { list-style: none; padding-left: 22px; font-size: 12px; font-weight: 300; }
  .contacts li { display: flex; align-items: center; gap: 10px; margin: 6px 0; }
  .contacts svg { width: 12px; height: 12px; fill: var(--brand-blue); flex: none; }
  .back__band {
    position: absolute; left: 0; right: 0; bottom: 0; height: 22px; background: var(--brand-blue);
  }
</style>
</head>
<body>
  <section class="card card--front">
    <div class="brand">
      <span class="brand__square"></span>
      <span class="brand__name">Ferncliff Advisory</span>
    </div>
    <div class="front__rule"><span class="front__site">www.ferncliffadvisory.com</span></div>
    <span class="front__base-line"></span>
  </section>

  <section class="card card--back">
    <div class="brand">
      <span class="brand__square"></span>
      <span class="brand__name">Ferncliff Advisory</span>
    </div>
    <div class="back__body">
      <div class="person">
        <p class="person__name">Daniel Whitcombe</p>
        <p class="person__role">Founder/CEO</p>
        <p class="person__address">2870 North 9th Avenue, Summit Floor,<br>Elm Ridge, Illinois 60531</p>
      </div>
      <span class="back__divider"></span>
      <ul class="contacts">
        <li><svg viewBox="0 0 24 24"><path d="M6.6 10.8a15.1 15.1 0 0 0 6.6 6.6l2.2-2.2a1 1 0 0 1 1-.25 11.4 11.4 0 0 0 3.6.57 1 1 0 0 1 1 1V20a1 1 0 0 1-1 1A17 17 0 0 1 3 4a1 1 0 0 1 1-1h3.5a1 1 0 0 1 1 1c0 1.25.2 2.45.57 3.6a1 1 0 0 1-.25 1z"/></svg>(855) 555 01472</li>
        <li><svg viewBox="0 0 24 24"><path d="M7 1h10a2 2 0 0 1 2 2v18a2 2 0 0 1-2 2H7a2 2 0 0 1-2-2V3a2 2 0 0 1 2-2zm0 3v14h10V4zm5 15.5a1 1 0 1 0 0 2 1 1 0 0 0 0-2z"/></svg>+1 312 555 0186</li>
        <li><svg viewBox="0 0 24 24"><path d="M2 5h20v14H2zm2 2v.5l8 5 8-5V7z"/></svg>dan@ferncliffadvisory.com</li>
        <li><svg viewBox="0 0 24 24"><path d="M12 2a10 10 0 1 0 0 20 10 10 0 0 0 0-20zm6.9 6h-3a15 15 0 0 0-1.4-3.9A8 8 0 0 1 18.9 8zM12 4c.8 1.2 1.5 2.5 1.9 4h-3.8c.4-1.5 1.1-2.8 1.9-4zM4.3 14a8 8 0 0 1 0-4h3.4a16 16 0 0 0 0 4zm.8 2h3a15 15 0 0 0 1.4 3.9A8 8 0 0 1 5.1 16zm3-8h-3a8 8 0 0 1 4.4-3.9A15 15 0 0 0 8.1 8zM12 20c-.8-1.2-1.5-2.5-1.9-4h3.8c-.4 1.5-1.1 2.8-1.9 4zm2.3-6H9.7a14 14 0 0 1 0-4h4.6a14 14 0 0 1 0 4zm.2 5.9a15 15 0 0 0 1.4-3.9h3a8 8 0 0 1-4.4 3.9zm1.8-5.9a16 16 0 0 0 0-4h3.4a8 8 0 0 1 0 4z"/></svg>www.ferncliffadvisory.com</li>
      </ul>
    </div>
    <span class="back__band"></span>
  </section>
</body>
</html>
```